Need Business Card for our Real Estate Business with Sales Executive's Picture

PANTONE 484 C ( RED)

PANTONE 2766 C ( BLUE

Industry/Entity Type

Real Estate

Contact Information for Business Card

Name, Mobile, email, & picture of Person
Agency Phone, address, Web address

Requirements
Must have
• Our Logo Colours, Agent Picture,

```html
<!DOCTYPE html>
<html lang="en">
<head>
<meta charset="utf-8">
<title>Meridian Real Estate – Business Card</title>
<link href="https://fonts.googleapis.com/css2?family=Cinzel:wght@400;500&family=Josefin+Sans:wght@300;400&display=swap" rel="stylesheet">
<style>
  :root {
    --stage: #1c1c1e;
    --paper: #ffffff;
    --brand-red: #9b2d2a;
    --brand-navy: #1f2a5c;
    --navy-deep: #23213f;
    --navy-mid: #2c3a70;
    --ink: #2a2f55;
    --photo-top: #e9edf3;
    --photo-suit: #2c3f86;
  }
  * { box-sizing: border-box; margin: 0; padding: 0; }
  html, body { width: 1200px; height: 864px; overflow: hidden; background: var(--stage); }
  .stage {
    position: relative; width: 1200px; height: 864px;
    display: flex; align-items: center; justify-content: center; gap: 40px;
  }
  .card {
    position: relative; width: 540px; height: 310px; overflow: hidden;
    box-shadow: 0 10px 30px rgba(0,0,0,.5);
  }

  /* Front */
  .card--front { background: var(--paper); }
  .agent-photo {
    position: absolute; left: 38px; top: 20px; width: 104px; height: 104px;
    border-radius: 50%; border: 2px solid var(--brand-navy); padding: 4px;
  }
  .agent-photo__fill {
    width: 100%; height: 100%; border-radius: 50%;
    background: linear-gradient(180deg, var(--photo-top) 0%, var(--photo-top) 45%, var(--photo-suit) 100%);
  }
  .agent-name {
    position: absolute; left: 40px; top: 134px;
    font: 400 20px/1 "Cinzel", serif; color: var(--brand-red); letter-spacing: .5px;
    text-transform: uppercase;
  }
  .company-name {
    position: absolute; right: 34px; top: 116px; text-align: center;
    font-family: "Cinzel", serif; font-weight: 500; color: var(--brand-navy);
  }
  .company-name__main { display: block; font-size: 28px; line-height: 1; letter-spacing: 3px; }
  .company-name__sub { display: block; font-size: 8px; line-height: 1; letter-spacing: 2px; margin-top: 4px; }
  .divider {
    position: absolute; left: 40px; right: 30px; top: 162px;
    height: 1.5px; background: var(--brand-red);
  }
  .contact-list {
    position: absolute; left: 40px; top: 176px; list-style: none;
  }
  .contact-list li {
    display: flex; align-items: center; gap: 10px; height: 22px;
    font: 400 13px/1 "Josefin Sans", sans-serif; color: var(--ink); letter-spacing: .5px;
  }
  .contact-list svg { width: 12px; height: 12px; fill: var(--brand-red); flex: none; }
  .office-address {
    position: absolute; right: 30px; top: 226px; text-align: left; font-style: normal;
    font: 400 13px/1.5 "Josefin Sans", sans-serif; color: var(--ink); letter-spacing: .5px;
  }

  /* Back */
  .card--back { background: linear-gradient(135deg, var(--navy-deep) 0%, var(--navy-mid) 100%); }
  .card--back svg.facets { position: absolute; inset: 0; }
  .back-name {
    position: absolute; left: 0; right: 0; top: 50%; transform: translateY(-50%);
    text-align: center; font-family: "Cinzel", serif; font-weight: 500; color: var(--paper);
  }
  .back-name__main { display: block; font-size: 34px; line-height: 1; letter-spacing: 4px; }
  .back-name__sub { display: block; font-size: 10px; line-height: 1; letter-spacing: 3px; margin-top: 6px; }
</style>
</head>
<body>
<main class="stage">
  <section class="card card--front">
    <div class="agent-photo"><div class="agent-photo__fill" role="img" aria-label="Portrait photo of the sales executive"></div></div>
    <h1 class="agent-name">Daniel Morrow</h1>
    <p class="company-name"><span class="company-name__main">MERIDIAN</span><span class="company-name__sub">REAL ESTATE</span></p>
    <div class="divider"></div>
    <ul class="contact-list">
      <li><svg viewBox="0 0 24 24"><path d="M6.6 10.8a15.1 15.1 0 0 0 6.6 6.6l2.2-2.2a1 1 0 0 1 1-.25 11.4 11.4 0 0 0 3.6.57 1 1 0 0 1 1 1V20a1 1 0 0 1-1 1A17 17 0 0 1 3 4a1 1 0 0 1 1-1h3.5a1 1 0 0 1 1 1c0 1.25.2 2.450.57 3.6a1 1 0 0 1-.25 1z"/></svg>(09) 414 7200</li>
      <li><svg viewBox="0 0 24 24"><path d="M7 1h10a2 2 0 0 1 2 2v18a2 2 0 0 1-2 2H7a2 2 0 0 1-2-2V3a2 2 0 0 1 2-2zm0 3v14h10V4zm5 15.5a1 1 0 1 0 0 2 1 1 0 0 0 0-2z"/></svg>027 515 3390</li>
      <li><svg viewBox="0 0 24 24"><path d="M2 5h20v14H2zm2 2v.5l8 5.5 8-5.5V7zm0 3v7h16v-7l-8 5.5z"/></svg>daniel@meridianrealestate.com</li>
      <li><svg viewBox="0 0 24 24"><path d="M12 2a10 10 0 1 0 0 20 10 10 0 0 0 0-20zm6.9 6h-3a15 15 0 0 0-1.4-3.9A8 8 0 0 1 18.9 8zM12 4c.8 1.1 1.5 2.5 1.9 4h-3.8c.4-1.5 1.1-2.9 1.9-4zM4.3 14a8 8 0 0 1 0-4h3.4a16 16 0 0 0 0 4zm.8 2h3a15 15 0 0 0 1.4 3.9A8 8 0 0 1 5.1 16zm3-8h-3a8 8 0 0 1 4.4-3.9A15 15 0 0 0 8.1 8zM12 20c-.8-1.1-1.5-2.5-1.9-4h3.8c-.4 1.5-1.1 2.9-1.9 4zm2.3-6H9.7a14 14 0 0 1 0-4h4.6a14 14 0 0 1 0 4zm.2 5.9a15 15 0 0 0 1.4-3.9h3a8 8 0 0 1-4.4 3.9zm1.8-5.9a16 16 0 0 0 0-4h3.4a8 8 0 0 1 0 4z"/></svg>www.meridianrealestate.com</li>
    </ul>
    <address class="office-address">2870 Lake Avenue Unit 410<br>Maple Grove, Il 60512</address>
  </section>

  <section class="card card--back">
    <svg class="facets" viewBox="0 0 540 310" preserveAspectRatio="none" aria-hidden="true">
      <polygon points="0,0 300,0 120,310 0,310" fill="#ffffff" opacity=".04"/>
      <polygon points="360,0 540,0 540,310 250,310" fill="#3a4d8f" opacity=".35"/>
      <polygon points="0,180 540,60 540,120 0,260" fill="#ffffff" opacity=".03"/>
    </svg>
    <p class="back-name"><span class="back-name__main">MERIDIAN</span><span class="back-name__sub">REAL ESTATE</span></p>
  </section>
</main>
</body>
</html>
```